Business Card Design for a Personal Trainer

I need a business card design for my job as a personal trainer. It should have a unique, modern and exclusive design. On the front there should be only my logo with my name and my job. 0162/3819204 Tobias Lendhart Wiesengrundweg 14 80417 Munich Germany The most important contact information is the web adress. it can be bigger than the rest, but its not necessary. The card should be 8,5cmx5,5cm big. Font: Roboto. Colors: black, white, gray, 56c1ff.

```html
<!DOCTYPE html>
<html lang="de">
<head>
<meta charset="utf-8">
<title>Tobias Lendhart – Personal Trainer Business Card</title>
<link rel="stylesheet" href="https://fonts.googleapis.com/css2?family=Roboto:wght@300;400;500&display=swap">
<style>
  :root {
    --stage: #2a2a2a;
    --card-white: #f4f4f4;
    --ink: #111111;
    --ink-soft: #222222;
    --link-blue: #2b3fe0;
    --photo-dark: #3a3a3a;
    --photo-mid: #7a7a7a;
    --photo-light: #b5b5b5;
  }
  * { box-sizing: border-box; margin: 0; padding: 0; }
  html, body {
    width: 1200px; height: 923px; overflow: hidden;
    background: var(--stage);
    font-family: "Roboto", sans-serif;
  }
  .sheet {
    width: 1200px; height: 923px;
    display: flex; flex-direction: column;
    align-items: center; justify-content: center; gap: 40px;
  }
  .card {
    position: relative;
    width: 620px; height: 401px;
    overflow: hidden;
    box-shadow: 0 10px 30px rgba(0,0,0,.45);
  }

  /* back side */
  .card--back {
    background: linear-gradient(135deg, var(--photo-light) 0%, var(--photo-mid) 45%, var(--photo-dark) 100%);
  }
  .card--back .back-photo { position: absolute; inset: 0; }
  .card--back .back-web {
    position: absolute; left: 0; right: 0; top: 250px;
    height: 34px; background: rgba(0,0,0,.28);
    color: #ffffff; font-weight: 300; font-size: 20px; letter-spacing: 1px;
    display: flex; align-items: center; justify-content: flex-end; padding-right: 40px;
  }

  /* front side */
  .card--front { background: var(--card-white); color: var(--ink); }
  .portrait {
    position: absolute; right: 28px; top: 40px;
    width: 200px; height: 290px;
    background: linear-gradient(180deg, var(--photo-light) 0%, var(--photo-mid) 35%, var(--photo-dark) 100%);
    border-radius: 90px 90px 0 0;
  }
  .brand {
    position: absolute; left: 52px; top: 92px; width: 300px;
    text-align: center;
  }
  .brand-name {
    display: flex; align-items: center; justify-content: center; gap: 10px;
    font-weight: 400; font-size: 27px; letter-spacing: .5px; color: var(--ink);
  }
  .brand-mark { width: 14px; height: 14px; background: var(--ink); }
  .brand-job {
    display: flex; align-items: center; gap: 8px;
    margin-top: 2px; font-size: 10px; letter-spacing: 3px; color: var(--ink-soft);
  }
  .brand-job::before, .brand-job::after {
    content: ""; flex: 1; height: 1px; background: var(--ink);
  }
  .divider {
    position: absolute; left: 38px; top: 180px;
    width: 330px; height: 1px; background: var(--ink);
  }
  .contact { position: absolute; left: 40px; top: 196px; }
  .contact-name { font-size: 26px; font-weight: 400; letter-spacing: .5px; }
  .contact-web { margin-top: 2px; font-size: 20px; font-weight: 300; color: var(--link-blue); }
  .contact-list { list-style: none; margin-top: 10px; margin-left: 16px; }
  .contact-list li {
    display: flex; align-items: center; gap: 10px;
    font-size: 16px; font-weight: 300; color: var(--ink-soft); line-height: 26px;
  }
  .contact-list svg { width: 14px; height: 14px; fill: var(--ink); flex: none; }
</style>
</head>
<body>
<main class="sheet">
  <section class="card card--back" aria-label="Card back">
    <div class="back-photo" role="img" aria-label="Black and white photo of an athlete lifting a loaded barbell"></div>
    <p class="back-web">www.tobiaslendhart.de</p>
  </section>

  <section class="card card--front" aria-label="Card front">
    <div class="portrait" role="img" aria-label="Black and white portrait of the trainer with arms crossed"></div>

    <div class="brand">
      <p class="brand-name"><span class="brand-mark"></span>TOBIAS LENDHART</p>
      <p class="brand-job">PERSONAL TRAINER</p>
    </div>

    <div class="divider"></div>

    <div class="contact">
      <p class="contact-name">Tobias Lendhart</p>
      <p class="contact-web">www.tobiaslendhart.de</p>
      <ul class="contact-list">
        <li>
          <svg viewBox="0 0 24 24" aria-hidden="true"><path d="M6.6 10.8a15 15 0 0 0 6.6 6.6l2.2-2.2c.3-.3.7-.4 1-.2 1.1.4 2.3.6 3.6.6.6 0 1 .4 1 1V20c0 .6-.4 1-1 1A17 17 0 0 1 3 4c0-.6.4-1 1-1h3.5c.6 0 1 .4 1 1 0 1.3.2 2.5.6 3.6.1.3 0 .7-.2 1z"/></svg>
          0162/3819204
        </li>
        <li>
          <svg viewBox="0 0 24 24" aria-hidden="true"><path d="M2 5h20v14H2zm2 2v.5l8 5 8-5V7l-8 5z"/></svg>
          t.lendhart@postfach-mail.de
        </li>
        <li>
          <svg viewBox="0 0 24 24" aria-hidden="true"><path d="M12 3 2 12h3v8h5v-5h4v5h5v-8h3z"/></svg>
          Wiesengrundweg 14, 80417 München
        </li>
      </ul>
    </div>
  </section>
</main>
</body>
</html>
```